Business Card Design

Attached is my current Business card I do not like it but I must save the logo portion of it. Don't like the color or the lettering am looking for more architectural look in grays or taupe with the green more of a charturese color and the blue a charcoal color on a textured paper that looks more like something high-end that would appeal to an architect or a designer. We make concrete decorative items such as concrete fireplaces, sinks, tops and more.

Target Market(s)

Architects designers of Commercial and Residential - artistic features

Industry/Entity Type

Architect

Contact Information for Business Card

Marisol T. Quenby President and Marketing Director
602-418-5093
email marisol@vantorelstone.example
Showroom "Quillmont Design Center" 4183 W Palomar Scottsdale AZ
Fax: 602-731-6624

Font styles to use
Sans Serif

Requirements
Must have
• Architectural
Natural and earthy colors with a touch of color in the existing attached

```html
<!DOCTYPE html>
<html lang="en">
<head>
<meta charset="utf-8">
<title>Marisol T. Quenby — Business Card</title>
<link href="https://fonts.googleapis.com/css2?family=Orbitron:wght@500;600&display=swap" rel="stylesheet">
<style>
  :root {
    --taupe: #b3a898;
    --taupe-light: #c4baab;
    --taupe-deep: #9f9483;
    --charcoal: #36383b;
    --charcoal-deep: #2b2d30;
    --chartreuse: #b4cc2a;
    --chartreuse-deep: #6f8510;
    --paper-light: #e6dfd3;
    --icon-grey: #a9a39a;
    --divider: #8fa51c;
  }
  * { margin: 0; padding: 0; box-sizing: border-box; }
  html, body {
    width: 1200px; height: 702px; overflow: hidden;
    background: #ffffff;
  }
  .card {
    position: relative;
    width: 1200px; height: 702px; overflow: hidden;
    background:
      repeating-linear-gradient(90deg, rgba(255,255,255,0.035) 0 2px, rgba(0,0,0,0.025) 2px 5px),
      repeating-linear-gradient(0deg, rgba(255,255,255,0.03) 0 3px, rgba(0,0,0,0.02) 3px 7px),
      radial-gradient(ellipse at 35% 30%, var(--taupe-light), var(--taupe) 55%, var(--taupe-deep) 100%);
    font-family: "Orbitron", "Arial", sans-serif;
    text-transform: uppercase;
  }
  .brand {
    position: absolute; right: 78px; top: 100px;
    display: flex; align-items: center; gap: 16px;
    color: var(--charcoal); font-weight: 600; font-size: 34px; letter-spacing: 4px;
  }
  .brand-square {
    width: 34px; height: 34px; background: var(--chartreuse);
  }
  .holder-name {
    position: absolute; right: 78px; top: 220px;
    color: var(--charcoal); font-weight: 600; font-size: 38px; letter-spacing: 5px;
  }
  .holder-title {
    position: absolute; right: 78px; top: 290px;
    color: var(--chartreuse-deep); font-weight: 600; font-size: 21px; letter-spacing: 2.5px;
  }
  .contact-band {
    position: absolute; left: 0; top: 470px; width: 1200px; height: 105px;
    background:
      repeating-linear-gradient(90deg, rgba(255,255,255,0.025) 0 2px, rgba(0,0,0,0.03) 2px 5px),
      linear-gradient(180deg, var(--charcoal-deep) 0%, var(--charcoal) 100%);
  }
  .contact-item {
    position: absolute; top: 0; height: 105px;
    display: flex; align-items: center; gap: 20px;
    color: var(--paper-light); font-weight: 500; font-size: 23px; letter-spacing: 2.5px;
  }
  .contact-email { left: 77px; }
  .contact-phone { right: 72px; }
  .office-band {
    position: absolute; left: 0; top: 575px; width: 1200px; height: 127px;
    background:
      repeating-linear-gradient(90deg, rgba(255,255,255,0.04) 0 2px, rgba(0,0,0,0.03) 2px 5px),
      var(--chartreuse);
    color: var(--charcoal);
  }
  .office-divider {
    position: absolute; left: 705px; top: 10px; width: 3px; height: 104px;
    background: var(--divider);
  }
  .office-heading {
    position: absolute; display: flex; align-items: center; gap: 12px;
    font-weight: 600; font-size: 20px; letter-spacing: 3px;
  }
  .fax-heading { left: 492px; top: 30px; }
  .showroom-heading { right: 70px; top: 12px; }
  .office-detail {
    position: absolute; font-weight: 500; font-size: 14px; letter-spacing: 2px;
  }
  .fax-number { left: 481px; top: 88px; }
  .showroom-address { right: 70px; top: 74px; text-align: right; line-height: 23px; }
</style>
</head>
<body>
<main class="card">
  <div class="brand"><span class="brand-square"></span>Vantorel Stone</div>

  <h1 class="holder-name">Marisol T. Quenby</h1>
  <p class="holder-title">President and Marketing Director</p>

  <section class="contact-band">
    <div class="contact-item contact-email">
      <svg width="62" height="40" viewBox="0 0 62 40" aria-hidden="true">
        <rect x="1" y="1" width="60" height="38" fill="var(--icon-grey)" stroke="#77726a" stroke-width="2"/>
        <polyline points="1,1 31,24 61,1" fill="none" stroke="#4f4c47" stroke-width="2"/>
        <line x1="1" y1="39" x2="24" y2="18" stroke="#4f4c47" stroke-width="2"/>
        <line x1="61" y1="39" x2="38" y2="18" stroke="#4f4c47" stroke-width="2"/>
      </svg>
      <span>marisol@vantorelstone.example</span>
    </div>
    <div class="contact-item contact-phone">
      <svg width="52" height="52" viewBox="0 0 52 52" aria-hidden="true">
        <rect x="0" y="0" width="52" height="52" rx="8" fill="var(--icon-grey)"/>
        <path d="M20 11 C15 13 14 18 16 25 C18 32 23 39 29 42 C33 44 36 42 38 39 L33 33 L29 35 C26 32 23 27 22 22 L26 19 Z" fill="#2b2d30"/>
      </svg>
      <span>602-418-5093</span>
    </div>
  </section>

  <section class="office-band">
    <div class="office-divider"></div>

    <div class="office-heading fax-heading">
      <svg width="42" height="28" viewBox="0 0 42 28" aria-hidden="true">
        <rect x="1" y="1" width="40" height="26" fill="none" stroke="var(--charcoal)" stroke-width="2"/>
        <polyline points="1,1 21,16 41,1" fill="none" stroke="var(--charcoal)" stroke-width="2"/>
        <line x1="1" y1="27" x2="16" y2="12" stroke="var(--charcoal)" stroke-width="2"/>
        <line x1="41" y1="27" x2="26" y2="12" stroke="var(--charcoal)" stroke-width="2"/>
      </svg>
      <span>Fax</span>
    </div>
    <p class="office-detail fax-number">602-731-6624</p>

    <div class="office-heading showroom-heading">
      <svg width="44" height="40" viewBox="0 0 44 40" aria-hidden="true">
        <polyline points="2,18 22,3 42,18" fill="none" stroke="var(--charcoal)" stroke-width="3"/>
        <rect x="7" y="16" width="30" height="22" fill="none" stroke="var(--charcoal)" stroke-width="3"/>
        <rect x="12" y="22" width="8" height="7" fill="var(--charcoal)"/>
        <rect x="25" y="22" width="7" height="16" fill="var(--charcoal)"/>
      </svg>
      <span>Showroom</span>
    </div>
    <p class="office-detail showroom-address">Quillmont Design Center<br>4183 W Palomar Scottsdale AZ</p>
  </section>
</main>
</body>
</html>
```